Brookvale Estates LLC stationary for a real estate property management company.

Create stationary (letterhead, envelopes, business cards) using Brookvale Estates LLC logo as primary creative element. Stationary design needs to be horizontal, leaving as much space as possible for correspondence copy. See attached Creative Brief and past stationary files for details.

Target Market(s)

Prospective apartment residents and current residents, vendors, and government agencies.

Industry/Entity Type

Property Management

Contact Information for Business Card

Business card employee title: Property Manager. Should include address, phone, fax, email, website, slogan, and Brookvale Estates logo.

Font styles to use
Sans Serif

Colors
0592cd
000000

Requirements
Must have
• Tone should be conservative, institutional, business (i.e. banking, finance, real estate). Must include: address, phone, fax, website, and slogan (see attached Creative Brief). Should be a horizontal design, leaving as much room as possible for letter correspondence copy.
Nice to have
• Please use an Arial or Helvetica style font.
Should not have
• Letterhead layout should leave as much room as possible for copy.

```html
<!DOCTYPE html>
<html lang="en">
<head>
<meta charset="utf-8">
<title>Brookvale Estates LLC – Stationery</title>
<link href="https://fonts.googleapis.com/css2?family=Arimo:wght@400;700&family=Open+Sans:wght@400&display=swap" rel="stylesheet">
<style>
  :root{
    --brand-blue:#0b6fb0;
    --brand-navy:#173a63;
    --ink:#2b2b2b;
    --muted:#555;
    --paper:#f4f5f6;
    --backdrop:#cfc4b4;
    --flap:#0d6fae;
  }
  *{box-sizing:border-box;margin:0;padding:0}
  html,body{width:1200px;height:754px;overflow:hidden}
  body{background:var(--backdrop);position:relative;font-family:Arimo,Arial,sans-serif;color:var(--ink)}
  .sheet{position:absolute;background:var(--paper);box-shadow:0 1px 4px rgba(0,0,0,.25)}

  .brand{display:flex;align-items:center;gap:6px;font-family:Arimo,Arial,sans-serif;font-weight:700;color:var(--brand-blue);white-space:nowrap}
  .brand-dot{border-radius:50%;background:var(--brand-blue);flex:none}

  .contact{list-style:none}
  .contact li{display:flex;align-items:center;gap:4px}
  .icon{width:8px;height:8px;fill:var(--brand-blue);flex:none}

  /* Letterhead */
  .letterhead{left:36px;top:32px;width:489px;height:690px}
  .letterhead .brand{position:absolute;left:47px;top:70px;font-size:17px}
  .letterhead .brand-dot{width:14px;height:14px}
  .letterhead .address{position:absolute;right:47px;top:45px;text-align:right;font-size:8px;line-height:10px;color:var(--ink)}
  .letterhead .contact{position:absolute;right:47px;top:68px;font-size:8px;line-height:10px;text-align:right}
  .letterhead .contact li{justify-content:flex-end}
  .letterhead .contact .icon{order:2}
  .letter{position:absolute;left:49px;top:194px;width:393px;font-family:"Open Sans",Arial,sans-serif;color:var(--muted)}
  .salutation{font-size:13px;color:#444;margin-bottom:24px}
  .letter p{font-size:7.4px;line-height:11.8px;margin-bottom:11.8px;text-align:justify}
  .sign-off{font-size:7.4px;margin-top:22px}
  .signature{width:62px;height:26px;margin-top:6px;background:linear-gradient(90deg,rgba(40,40,40,.0),rgba(40,40,40,.25),rgba(40,40,40,.0))}

  /* Business card */
  .card{left:716px;top:106px;width:314px;height:178px;background:#eef0f1}
  .card .brand{position:absolute;left:18px;top:22px;font-size:19px;color:var(--brand-navy)}
  .card .brand-dot{width:15px;height:15px;background:var(--brand-navy)}
  .card .person{position:absolute;left:18px;top:62px}
  .person .name{font-size:11px;font-weight:700;color:var(--brand-navy);letter-spacing:.2px}
  .person .role{font-size:8.5px;color:var(--ink);margin-top:1px}
  .card .address{position:absolute;left:18px;top:88px;font-size:7.5px;line-height:9.5px}
  .card .contact{position:absolute;left:18px;top:111px;font-size:7.5px;line-height:10px}
  .card .contact .icon{fill:var(--brand-navy)}
  .card .slogan{position:absolute;left:18px;top:156px;font-size:7.8px;font-weight:700;color:var(--brand-blue)}

  /* Envelope back */
  .envelope-back{left:615px;top:349px;width:548px;height:250px;background:#ebeced}
  .envelope-back .flap{position:absolute;left:0;top:0;width:548px;height:92px}
  .flap-mark{position:absolute;left:0;right:0;top:22px;display:flex;flex-direction:column;align-items:center;gap:6px}
  .flap-mark .brand-dot{width:28px;height:28px;background:#fff}
  .flap-mark .url{font-size:7.5px;color:#fff}

  /* Envelope front */
  .envelope-front{left:547px;top:471px;width:550px;height:250px}
  .envelope-front .brand{position:absolute;left:24px;top:38px;font-size:16px}
  .envelope-front .brand-dot{width:13px;height:13px}
  .envelope-front .address{position:absolute;left:38px;top:68px;font-size:7.5px;line-height:9.5px}
</style>
</head>
<body>
<svg width="0" height="0" style="position:absolute">
  <defs>
    <symbol id="i-phone" viewBox="0 0 10 10"><path d="M2 0.8l1.6 0 .6 2.2-1 .8c.6 1.3 1.5 2.2 2.8 2.8l.8-1 2.2.6 0 1.6c0 .6-.5 1-1 1C4 8.8 1.2 6 1 1.8c0-.5.4-1 1-1z"/></symbol>
    <symbol id="i-fax" viewBox="0 0 10 10"><rect x="2.5" y="0.8" width="5" height="3"/><rect x="0.8" y="3.8" width="8.4" height="4.2" rx=".6"/><rect x="2.5" y="6.8" width="5" height="2.4" fill="#fff"/></symbol>
    <symbol id="i-mail" viewBox="0 0 10 10"><rect x="0.8" y="2" width="8.4" height="6" rx=".5"/><path d="M1 2.4l4 3 4-3" stroke="#fff" stroke-width=".9" fill="none"/></symbol>
    <symbol id="i-web" viewBox="0 0 10 10"><circle cx="5" cy="5" r="4.2"/><path d="M1 5h8M5 1c-2 2.5-2 5.5 0 8M5 1c2 2.5 2 5.5 0 8" stroke="#fff" stroke-width=".7" fill="none"/></symbol>
  </defs>
</svg>

<section class="sheet letterhead">
  <div class="brand"><span class="brand-dot"></span>Brookvale Estates LLC</div>
  <address class="address" style="font-style:normal">2710 Alder Creek Road #B210<br>Fresno, CA 93711</address>
  <ul class="contact">
    <li>555-214-7730<svg class="icon"><use href="#i-phone"/></svg></li>
    <li>555-214-7731<svg class="icon"><use href="#i-fax"/></svg></li>
    <li>daniel@brookvaleestates.us<svg class="icon"><use href="#i-mail"/></svg></li>
    <li>www.brookvaleestates.us<svg class="icon"><use href="#i-web"/></svg></li>
  </ul>
  <div class="letter">
    <p class="salutation">Dear Mr. Collins,</p>
    <p>Lorem ipsum dolor sit amet, consectetur adipiscing elit. Donec orci purus, luctus vitae dignissim eu, iaculis sed purus. Vivamus faucibus, ipsum nec aliquet viverra, leo mauris condimentum ligula, sit amet sagittis enim ligula quis arcu. Nam egestas tortor id nisi porttitor mattis. In tortor ante, ultricies in suscipit a, tempus non massa. Vivamus et auctor mi. Fusce vel massa nulla. Phasellus nec eros mauris, et scelerisque orci.</p>
    <p>Donec malesuada orci vitae nulla accumsan porta a id massa. Quisque accumsan iaculis magna sit amet fringilla. Maecenas consequat, magna eget tincidunt semper, odio nibh rutrum mi, id feugiat ante nisi eu risus. Vestibulum nunc orci, rhoncus a placerat in, ultricies in mi. Cras mattis varius eros, vel fringilla nisi suscipit eget. Quisque scelerisque sagittis nulla at porttitor.</p>
    <p>Sed id augue vitae urna euismod commodo aliquet a quam. Pellentesque arcu velit, cursus et malesuada ut, consequat et diam. Nullam erat sem, rhoncus id ullamcorper vitae, rhoncus et arcu. In ultricies ultricies nulla, ut rutrum nisi iaculis at. Donec eu magna a metus ornare faucibus. Fusce aliquet faucibus ultricies. Morbi semper, est id tincidunt gravida, sem arcu adipiscing lacus, ac bibendum nulla leo eu purus. Quisque nec diam sed risus consectetur a accumsan quis quis nibh. Vestibulum id purus lorem.</p>
    <p>It is a long established fact that a reader will be distracted by the readable content of a page when looking at its layout. The point of using Lorem Ipsum is that it has a more-or-less normal distribution of letters, as opposed to using 'Content here, content here', making it look like readable English. Many desktop publishing packages</p>
    <p class="sign-off">Sincerely,</p>
    <div class="signature" role="img" aria-label="Handwritten signature"></div>
  </div>
</section>

<section class="sheet card">
  <div class="brand"><span class="brand-dot"></span>Brookvale Estates LLC</div>
  <div class="person">
    <div class="name">DANIEL HARPER</div>
    <div class="role">Property Manager</div>
  </div>
  <address class="address" style="font-style:normal">2710 Alder Creek Road #B210<br>Fresno, CA 93711</address>
  <ul class="contact">
    <li><svg class="icon"><use href="#i-phone"/></svg>555-214-7730</li>
    <li><svg class="icon"><use href="#i-fax"/></svg>555-214-7731</li>
    <li><svg class="icon"><use href="#i-mail"/></svg>daniel@brookvaleestates.us</li>
    <li><svg class="icon"><use href="#i-web"/></svg>www.brookvaleestates.us</li>
  </ul>
  <div class="slogan">Multifamily Property Management</div>
</section>

<section class="sheet envelope-back">
  <svg class="flap" viewBox="0 0 548 92" preserveAspectRatio="none">
    <path d="M0 0H548L539 62Q535 92 505 92H43Q13 92 9 62Z" fill="var(--flap)"/>
  </svg>
  <div class="flap-mark">
    <span class="brand-dot"></span>
    <span class="url">www.brookvaleestates.us</span>
  </div>
</section>

<section class="sheet envelope-front">
  <div class="brand"><span class="brand-dot"></span>Brookvale Estates LLC</div>
  <address class="address" style="font-style:normal">2710 Alder Creek Road #B210<br>Fresno, CA 93711</address>
</section>
</body>
</html>
```